Bold, Modern, Clean "Kestrelwaymassage.com" website

Why we stand out?
We are a male and female mobile massage team. Our names are Paul and Lina. 
Kestrel Way is a Seattle based mobile massage service. Our massage is offered to the community with a goal of facilitating balance within each individual. We specialize in integrated Pain management, and sports/medical massage therapy. Every client's first assessment is attended by our male and female massage therapist team. Depending on the goals identified for an individual determines which therapist will be assigned to provide treatment, if not both.

Our passion...
Here at Kestrel Way, we have a great passion for Postural Resoration and how it is integrated into an individual's Massage treatment. We pride ourselves in being natural facilitators of healing, which takes the ego of the therapist out of the client's healing process. We strive to deliver the best massage possible by including modalities such as Neuromuscular, Myofascial release, spontaneous muscle release, postural restoration, orthopedic, and medical massage.

Our education...

We are both Graduates of Venmora, school of massage therapy. We have continuing education in medical massage, myofacial release, trigger point therapy, postural restoration, anatomy, and spontaneous muscle release. Lina is also a Certified Yoga Instructor, which amplifies her experience with flexibility and strength as it pertains to each individual. Paul's passion is Massage, stretching, and strength training to encourage postural restoration and realignment.

Our rates-

Our rates are $75/ 60 minutes, $95/ 90 minutes, and $120/ 120 minutes.

Education-
Both Lina and I worked as behavioral health professionals that specialized in life skills mentoring for youth who had experienced different types of trauma. This led us both to want to help others in a different environment, where individuals can be empowered to take responsibility over their own healing. To us, massage is a type of manipulation physical therapy, that encourages healing on many levels.

Advice to any massage client-
The most important thing to 'us', as Licenced providers is to get you on to our table to show you our skills. But a good therapist never forgets that it's not about what we do for you, but what we can facilitate for you. Your health and healing has nothing to do with us. It is yours, not ours. Identify what your goals are with any Therapist, and know what the end looks like. Progress should be tangible, such as range of motion, and decreased pain.

Lina and Paul at Kestrel Way are awesome! I recently had open heart surgery, and Lina worked on me to increase my range of motion while helping with the pinched nerve from my arm being in the same position for so long during my surgery. My wife drives a lot for work, and Paul has helped decrease her neck and lower back pain immensely. They are seriously the best therapists I have ever worked with. I would recommend them to anyone who needs anything from stress relief to a medical massage treatment. They are professional, up beat, easy going, and always on time. And, I love that they meet us where ever we like! We did a staycation recently, where they came to our hotel to give us relaxation massages. Although usually they come to our home, where we focus on pain related issues. We will continue to work with them for a long, long time.

Target Market(s)

Mobile massage therapy clients

Industry/Entity Type

Massage Therapy

Coding

Coded - Design and coding required

Number of Pages Required

1 page

Font styles to use
Serif
Sans Serif

Requirements
Must have
• Please add or remove any information that would help the presentation of our website. Our logo is posted below, please include into the website.
• Please include a contact field that includes, kestrelwaymassage@fernmail.net,
• (206) 555-0148
• We have also included our own stock photos, as well as a photo of Paul and Lina. Please include a cropped photo of both massage therapists.

```html
<!DOCTYPE html>
<html lang="en">
<head>
<meta charset="utf-8">
<title>Kestrel Way mobile massage</title>
<link rel="stylesheet" href="https://fonts.googleapis.com/css2?family=Open+Sans:wght@300;400;600&family=Roboto:wght@400;500;700&display=swap">
<style>
:root{
  --teal:#00bfae;
  --teal-light:#00d6c3;
  --teal-deep:#008a7c;
  --teal-dark:#004d4a;
  --teal-night:#003b39;
  --ink:#222;
  --body:#3a3a3a;
  --grey-band:#efefef;
  --rule:#d6d6d6;
  --white:#fff;
  --logo-blue:#1f3fc4;
}
*{margin:0;padding:0;box-sizing:border-box}
html,body{width:1200px;height:2643px;overflow:hidden;background:var(--white)}
body{position:relative;font-family:"Open Sans",Arial,sans-serif;color:var(--body)}
.abs{position:absolute}

/* hero */
.hero{position:absolute;left:0;top:0;width:1200px;height:678px}
.hero svg{position:absolute;left:0;top:0}
.brand{position:absolute;display:flex;align-items:center;gap:14px;font-family:"Roboto",Arial,sans-serif;font-weight:700;color:var(--white);letter-spacing:1px}
.brand .dot{border-radius:50%;background:var(--logo-blue)}
.hero .brand{left:128px;top:76px;font-size:30px}
.hero .brand .dot{width:46px;height:46px}
.nav-label{position:absolute;font-family:"Roboto",Arial,sans-serif;font-size:22px;color:var(--white);line-height:1}

/* services */
.services{position:absolute;left:0;top:678px;width:1200px;height:300px;display:flex}
.service{width:300px;height:300px;display:flex;flex-direction:column}
.service-title{height:71px;display:flex;align-items:center;justify-content:center;font-family:"Roboto",Arial,sans-serif;font-weight:700;font-size:16px;color:var(--white)}
.service-body{flex:1;display:flex;flex-direction:column;align-items:center;padding-top:30px}
.service-icon{width:50px;height:50px;border-radius:50%;background:rgba(255,255,255,.85);margin-bottom:26px}
.service-body p{width:250px;text-align:center;font-size:14.5px;line-height:26px;color:var(--white)}
.s1 .service-title{background:#007d71}.s1 .service-body{background:var(--teal-light)}
.s2 .service-title{background:#00978a}.s2 .service-body{background:#00b6a6}
.s3 .service-title{background:var(--teal-dark)}.s3 .service-body{background:#009c8e}
.s4 .service-title{background:var(--teal-night)}.s4 .service-body{background:var(--teal-deep)}

/* sections */
.section-title{position:absolute;left:0;width:1200px;text-align:center;font-weight:300;font-size:41px;color:var(--ink);line-height:1}
.section-text{position:absolute;left:140px;width:920px;text-align:center;font-size:14.5px;line-height:26px;color:var(--body)}
.divider{position:absolute;left:319px;width:562px;height:40px}
.btn{position:absolute;height:57px;display:flex;align-items:center;justify-content:center;font-family:"Roboto",Arial,sans-serif;font-size:17px;color:var(--ink);border-radius:3px}
.btn-fill{background:linear-gradient(var(--teal-light),var(--teal));box-shadow:0 3px 0 #009b8d}
.btn-line{border:2px solid var(--teal);background:var(--white)}

.testimonials{position:absolute;left:0;top:1380px;width:1200px;height:417px;background:radial-gradient(ellipse at 30% 40%,#6b4a35 0%,#3a2a20 45%,#1c1410 100%)}
.testimonials .section-title,.testimonials .section-text{color:var(--white)}
.quote-name{position:absolute;left:0;top:287px;width:1200px;text-align:center;font-size:24px;color:var(--white)}
.dots{position:absolute;left:545px;top:360px;display:flex;gap:11px}
.dots span{width:10px;height:10px;background:var(--white)}
.dots span.off{background:transparent;border:2px solid var(--white)}

.contact-strip{position:absolute;left:0;top:2225px;width:1200px;height:104px;background:var(--grey-band)}
.contact-icon{position:absolute;width:63px;height:58px;background:var(--teal);border-radius:2px;display:flex;align-items:center;justify-content:center}
.contact-text{position:absolute;font-size:23px;color:#333;line-height:1}

.footer{position:absolute;left:0;top:2329px;width:1200px;height:314px;background:var(--teal-deep)}
.footer .brand{left:0;width:1200px;justify-content:center;top:72px;font-size:26px}
.footer .brand .dot{width:40px;height:40px}
.socials{position:absolute;left:458px;top:171px;display:flex;gap:10px}
.socials span{width:63px;height:58px;border:2px solid rgba(255,255,255,.85);border-radius:2px}
.socials span.active{background:var(--teal);border-color:var(--teal)}
.copyright{position:absolute;left:0;top:248px;width:1200px;text-align:center;font-size:14.5px;color:var(--white)}
</style>
</head>
<body>

<header class="hero">
  <svg width="1200" height="678" viewBox="0 0 1200 678">
    <defs>
      <linearGradient id="heroPhoto" x1="0" y1="0" x2="1" y2="1">
        <stop offset="0" stop-color="#5a3c28"/>
        <stop offset=".45" stop-color="#b4865c"/>
        <stop offset="1" stop-color="#e7cdb4"/>
      </linearGradient>
      <clipPath id="panelClip"><path d="M0 0 H414 Q352 339 424 678 H0 Z"/></clipPath>
    </defs>
    <rect width="1200" height="678" fill="url(#heroPhoto)" role="img" aria-label="Photo of a therapist giving a back massage to a relaxed client"/>
    <g clip-path="url(#panelClip)">
      <rect width="440" height="678" fill="#1e1612" opacity=".9"/>
      <rect y="292" width="440" height="82" fill="#0f6f66" opacity=".85"/>
      <rect y="374" width="440" height="84" fill="#3a2a48" opacity=".8"/>
      <rect y="458" width="440" height="83" fill="#4a3b30" opacity=".7"/>
      <rect y="541" width="440" height="84" fill="#3d3028" opacity=".75"/>
    </g>
    <g stroke="#fff" stroke-width="2" fill="none">
      <line x1="247" y1="248" x2="398" y2="248"/><circle cx="405" cy="248" r="7"/>
      <line x1="264" y1="333" x2="416" y2="333"/><circle cx="423" cy="333" r="7"/>
      <line x1="264" y1="414" x2="416" y2="414"/><circle cx="423" cy="414" r="7"/>
      <line x1="275" y1="499" x2="426" y2="499"/><circle cx="433" cy="499" r="7"/>
      <line x1="291" y1="581" x2="444" y2="581"/><circle cx="451" cy="581" r="7"/>
    </g>
    <g fill="#fff">
      <circle cx="405" cy="248" r="2.5"/><circle cx="423" cy="333" r="2.5"/><circle cx="423" cy="414" r="2.5"/><circle cx="433" cy="499" r="2.5"/><circle cx="451" cy="581" r="2.5"/>
      <path d="M440 249 L452 238 L464 249 H460 V259 H455 V252 H449 V259 H444 V249 Z"/>
      <circle cx="453" cy="328" r="6"/><path d="M443 344 Q443 335 453 335 Q463 335 463 344 Z"/>
      <path d="M440 412 L457 405 L474 412 L457 419 Z"/><path d="M447 416 V423 Q457 428 467 423 V416 L457 420 Z"/>
      <ellipse cx="467" cy="496" rx="11" ry="8"/><path d="M460 501 L457 508 L465 503 Z"/>
      <rect x="475" y="569" width="12" height="22" rx="2"/>
    </g>
    <rect x="478" y="573" width="6" height="13" fill="#3d3028"/>
  </svg>
  <div class="brand"><span class="dot"></span>KESTREL WAY</div>
  <a class="nav-label" style="left:169px;top:237px">HOME</a>
  <a class="nav-label" style="left:150px;top:322px">ABOUT US</a>
  <a class="nav-label" style="left:143px;top:403px">EDUCATION</a>
  <a class="nav-label" style="left:132px;top:488px">TESTIMONIAL</a>
  <a class="nav-label" style="left:137px;top:570px">CONTACT US</a>
</header>

<section class="services">
  <div class="service s1"><div class="service-title">Neuromuscular</div><div class="service-body"><div class="service-icon" role="img" aria-label="Flexed arm icon"></div><p>Lorem ipsum dolor sit amet, consectetur adipiscing elit, sed do eiusmod tempor incididunt ut labore et dolore magna aliqua.</p></div></div>
  <div class="service s2"><div class="service-title">Spontaneous Muscle Release</div><div class="service-body"><div class="service-icon" role="img" aria-label="Strong figure icon"></div><p>Lorem ipsum dolor sit amet, consectetur adipiscing elit, sed do eiusmod tempor incididunt ut labore et dolore magna aliqua.</p></div></div>
  <div class="service s3"><div class="service-title">postural restoration</div><div class="service-body"><div class="service-icon" role="img" aria-label="Stretching figure icon"></div><p>Lorem ipsum dolor sit amet, consectetur adipiscing elit, sed do eiusmod tempor incididunt ut labore et dolore magna aliqua.</p></div></div>
  <div class="service s4"><div class="service-title">Medical Massage</div><div class="service-body"><div class="service-icon" role="img" aria-label="Meditating figure icon"></div><p>Lorem ipsum dolor sit amet, consectetur adipiscing elit, sed do eiusmod tempor incididunt ut labore et dolore magna aliqua.</p></div></div>
</section>

<section class="education">
  <h2 class="section-title" style="top:1032px">See Our Education</h2>
  <svg class="divider" style="top:1087px" viewBox="0 0 562 40">
    <g stroke="#ddd" stroke-width="2"><line x1="0" y1="18" x2="254" y2="18"/><line x1="0" y1="22" x2="254" y2="22"/><line x1="308" y1="18" x2="562" y2="18"/><line x1="308" y1="22" x2="562" y2="22"/></g>
    <path d="M260 17 L281 9 L302 17 L281 25 Z M270 21 V29 Q281 34 292 29 V21 L281 25 Z" fill="#888"/>
  </svg>
  <p class="section-text" style="top:1152px">We are both Graduates of Venmora, school of massage therapy. We have continuing education in medical massage, my facial release, trigger point therapy, postural restoration, anatomy, and spontaneous muscle release. Lina is also a Certified Yoga Instructor, which amplifies her experience with flexibility and strength as it pertains to each individual</p>
  <a class="btn btn-fill" style="left:428px;top:1272px;width:166px">READ MORE</a>
  <a class="btn btn-line" style="left:604px;top:1272px;width:166px">OUR RATE</a>
</section>

<section class="testimonials" role="img" aria-label="Dim photo of a massage with candles">
  <h2 class="section-title" style="top:59px">What Our Clients Say</h2>
  <svg class="divider" style="top:114px" viewBox="0 0 562 40">
    <g stroke="#fff" stroke-width="2"><line x1="0" y1="18" x2="254" y2="18"/><line x1="0" y1="22" x2="254" y2="22"/><line x1="308" y1="18" x2="562" y2="18"/><line x1="308" y1="22" x2="562" y2="22"/></g>
    <ellipse cx="278" cy="17" rx="14" ry="10" fill="#fff"/><ellipse cx="290" cy="24" rx="11" ry="8" fill="#fff"/><path d="M268 24 L264 32 L274 26 Z" fill="#fff"/>
  </svg>
  <p class="section-text" style="top:189px">Lina and Paul at Kestrel Way are awesome! I recently had open heart surgery, and Lina worked on me to increase my range of motion while helping with the pinched nerve from my arm being in the same position for so long during my surgery. My wife drives a lot for work, and Paul has helped decrease her neck and lower back pain immensely. They are seriously the best therapists I have ever worked with</p>
  <p class="quote-name">- Darcy T.</p>
  <div class="dots"><span></span><span class="off"></span><span></span><span></span><span></span><span></span></div>
</section>

<section class="about">
  <h2 class="section-title" style="top:1850px">Know About Us</h2>
  <svg class="divider" style="top:1901px" viewBox="0 0 562 40">
    <g stroke="#ddd" stroke-width="2"><line x1="0" y1="18" x2="254" y2="18"/><line x1="0" y1="22" x2="254" y2="22"/><line x1="308" y1="18" x2="562" y2="18"/><line x1="308" y1="22" x2="562" y2="22"/></g>
    <circle cx="281" cy="9" r="8" fill="#888"/><path d="M266 36 Q266 19 281 19 Q296 19 296 36 Z" fill="#888"/>
  </svg>
  <p class="section-text" style="top:1960px">We are a male and female mobile massage team. Our names are Paul and Lina.<br>Kestrel Way is a Seattle based mobile massage service. Our massage is offered to the community with a goal of facilitating balance within each individual. We specialize in integrated Pain management, and sports/medical massage therapy. Every client's first assessment is attended by our male and female massage therapist team.</p>
  <a class="btn btn-fill" style="left:516px;top:2116px;width:166px">READ MORE</a>
</section>

<section class="contact-strip">
  <div class="contact-icon" style="left:236px;top:25px"><svg width="26" height="26" viewBox="0 0 24 24"><path fill="#fff" d="M6.6 10.8a15 15 0 0 0 6.6 6.6l2.2-2.2c.3-.3.7-.4 1-.2 1.1.4 2.3.6 3.6.6.6 0 1 .4 1 1V20c0 .6-.4 1-1 1A17 17 0 0 1 3 4c0-.6.4-1 1-1h3.5c.6 0 1 .4 1 1 0 1.3.2 2.5.6 3.6.1.3 0 .7-.2 1z"/></svg></div>
  <span class="contact-text" style="left:317px;top:41px">(206) 555-0148</span>
  <div class="contact-icon" style="left:580px;top:25px"><svg width="26" height="20" viewBox="0 0 26 20"><rect x="1" y="1" width="24" height="18" rx="2" fill="#fff"/><path d="M2 3 L13 11 L24 3" stroke="#00bfae" stroke-width="2" fill="none"/></svg></div>
  <span class="contact-text" style="left:659px;top:41px">kestrelwaymassage@fernmail.net</span>
</section>

<footer class="footer">
  <div class="brand"><span class="dot"></span>KESTREL WAY</div>
  <div class="socials" aria-label="Social links"><span class="active"></span><span></span><span></span><span></span></div>
  <p class="copyright">© Kestrel Way mobile massage - 2015. All rights reserved.</p>
</footer>

</body>
</html>
```